SaaS Early tech startup business card design

Unique design for experience ecommerce platform company. the business cards will be used by executive members. conformance with color code is required.

```html
<!DOCTYPE html>
<html lang="en">
<head>
<meta charset="utf-8">
<title>Velqo Business Card</title>
<link href="https://fonts.googleapis.com/css2?family=Lato:wght@400;700;900&display=swap" rel="stylesheet">
<style>
  :root {
    --bg: #1c1c1c;
    --deep-blue: #0b6890;
    --mid-blue: #0f7d96;
    --teal: #00b39a;
    --teal-light: #3ec3ad;
    --white: #ffffff;
    --ink: #2a2a2a;
  }
  * { margin: 0; padding: 0; box-sizing: border-box; }
  html, body { width: 1200px; height: 1015px; overflow: hidden; }
  body {
    background: var(--bg);
    font-family: "Lato", sans-serif;
    position: relative;
  }
  .card {
    position: absolute;
    left: 250px;
    width: 700px;
    height: 400px;
    overflow: hidden;
    box-shadow: 0 12px 30px rgba(0,0,0,.55);
  }
  .card-front {
    top: 70px;
    background: linear-gradient(150deg, var(--deep-blue) 0%, #0a8a9c 45%, var(--teal) 100%);
    display: flex;
    align-items: center;
    justify-content: center;
  }
  .brand-name {
    font-family: "Lato", sans-serif;
    font-weight: 900;
    font-size: 120px;
    letter-spacing: 2px;
    color: var(--teal-light);
    line-height: 1;
  }
  .card-back {
    top: 545px;
    background: var(--white);
  }
  .wave { position: absolute; inset: 0; }
  .card-back .brand-name {
    position: absolute;
    left: 70px;
    top: 118px;
    font-size: 92px;
    color: var(--mid-blue);
  }
  .identity {
    position: absolute;
    right: 40px;
    top: 36px;
    text-align: right;
  }
  .person-name {
    font-weight: 700;
    font-size: 22px;
    letter-spacing: 1px;
    color: #12969a;
    text-transform: uppercase;
  }
  .person-role {
    font-size: 16px;
    color: var(--ink);
    margin-top: 2px;
  }
  .contact {
    position: absolute;
    right: 34px;
    top: 192px;
    list-style: none;
    color: var(--white);
    font-size: 16px;
    text-align: right;
  }
  .contact li {
    display: flex;
    justify-content: flex-end;
    align-items: flex-start;
    gap: 10px;
    line-height: 1.35;
  }
  .contact .address { margin-top: 6px; }
  .contact svg { width: 15px; height: 15px; flex: none; margin-top: 3px; }
</style>
</head>
<body>
  <section class="card card-front" aria-label="Card front">
    <span class="brand-name">velqo</span>
  </section>

  <section class="card card-back" aria-label="Card back">
    <svg class="wave" viewBox="0 0 700 400" preserveAspectRatio="none" aria-hidden="true">
      <defs>
        <linearGradient id="waveFill" x1="0" y1="0" x2="1" y2="1">
          <stop offset="0" stop-color="#4cc4ad"/>
          <stop offset="1" stop-color="#00b39a"/>
        </linearGradient>
      </defs>
      <path d="M0,348 C200,358 300,322 400,238 S560,150 700,150 L700,400 L0,400 Z" fill="url(#waveFill)"/>
      <path d="M0,315 C190,330 290,300 385,220 S540,128 680,128" fill="none" stroke="var(--mid-blue)" stroke-width="9"/>
      <path d="M0,332 C195,343 295,312 392,229 S550,139 700,139" fill="none" stroke="var(--deep-blue)" stroke-width="4"/>
    </svg>

    <span class="brand-name">velqo</span>

    <div class="identity">
      <p class="person-name">Marcus Hale</p>
      <p class="person-role">Managing Director</p>
    </div>

    <ul class="contact">
      <li>044-555 010 220
        <svg viewBox="0 0 24 24"><path fill="#fff" d="M6.6 10.8a15 15 0 0 0 6.6 6.6l2.2-2.2c.3-.3.7-.4 1-.2 1.1.4 2.3.6 3.6.6.6 0 1 .4 1 1V20c0 .6-.4 1-1 1A17 17 0 0 1 3 4c0-.6.4-1 1-1h3.5c.6 0 1 .4 1 1 0 1.3.2 2.5.6 3.6.1.3 0 .7-.2 1z"/></svg>
      </li>
      <li>hello@velqo.io
        <svg viewBox="0 0 24 24"><path fill="#fff" d="M2 5h20v14H2z"/><path d="M2 5l10 8 10-8" fill="none" stroke="#1bb9a2" stroke-width="2"/></svg>
      </li>
      <li>www.velqo.io
        <svg viewBox="0 0 24 24" fill="none" stroke="#fff" stroke-width="2"><circle cx="12" cy="12" r="10"/><path d="M2 12h20M12 2c3 3 3 17 0 20M12 2c-3 3-3 17 0 20"/></svg>
      </li>
      <li class="address">87, Harbour Lane<br>Northbay, 30918
        <svg viewBox="0 0 24 24"><path fill="#fff" d="M12 2a7 7 0 0 0-7 7c0 5 7 13 7 13s7-8 7-13a7 7 0 0 0-7-7zm0 9.5a2.5 2.5 0 1 1 0-5 2.5 2.5 0 0 1 0 5z"/></svg>
      </li>
    </ul>
  </section>
</body>
</html>
```